New Organic Skin Care Line Needs to Design a Product Label

***THE WINNER OF THIS PROJECT WILL MOST LIKELY BECOME THE EXCLUSIVE DESIGNER FOR OUR OTHER PRODUCT LABELS***

We need a label design for a new organic skin care product line called "Maple Dew Gala." This specific product is a 100% pure organic coconut oil. It's used for skin hydration, protection, and makeup removal.

Info to include on front label:

1. Logo: Maple Dew Gala (attached)
2. Product Name: Pure Coconut Oil (emphasize "organic" somewhere)
3. Slogan: Hydrate your skin and hair.
4. Size: 8 FL OZ 236mL

Attached is:

1. The brand logo "Maple Dew Gala" with a white background.
2. An image of the bottle we will use.
3. An image of the bottle with lines to show the size and placement of the label.
4. The brand logo "Maple Dew Gala" with a black background. (photoshop file)

What we need:

A simple mock up of the front side of the label on the bottle. We first want to know what it will look like on the bottle given the size and dimensions.

- We would like one label with a white background (including the logo with a white background).
- We would like a second label with a black background (including the logo with a black background, just need to make the black font white instead of black).

We can get a great idea of what to expect from the front side of the label so we will complete the back side once we identify a winner.
Updates

Apologies, but we are now using a different bottle. The previous one is now discontinued. Please view the two most recent images uploaded. One is an image of the new bottle by itself. The other is an image of that bottle with instructions. Please use your most recent designs on the new bottle. Feel free to make any modifications you see fit to compliment the new bottle shape. Added Friday, March 18, 2016

Reason: We are still working with the label company to finalize the size. Once the size is confirmed we will have to tweak labels based on finalized measurements.

Target Market(s)

Women, 18-70

Industry/Entity Type

Skin Care Product

Font styles to use
Decorative
Script

Requirements
Must have
• -"shabby sheek" and "cute" theme
• -soft organic feel
• -the ingredients are organic, pure, and natural. That should be an essence of the label.

```html
<!DOCTYPE html>
<html lang="en">
<head>
<meta charset="utf-8">
<title>Maple Dew Gala – Pure Coconut Oil Label</title>
<link href="https://fonts.googleapis.com/css2?family=Libre+Baskerville&family=Didact+Gothic&display=swap" rel="stylesheet">
<style>
  :root {
    --page: #f2f2f2;
    --label: #ffffff;
    --ink: #1c1c1c;
    --accent: #e8227f;
    --leaf-tone: #d9d9d9;
  }
  html, body {
    margin: 0;
    padding: 0;
    width: 716px;
    height: 1200px;
    overflow: hidden;
    background: var(--page);
  }
  .canvas {
    position: relative;
    width: 716px;
    height: 1200px;
  }
  .label-shape {
    position: absolute;
    left: 0;
    top: 0;
  }
  .label-text {
    position: absolute;
    left: 0;
    width: 716px;
    text-align: center;
    color: var(--ink);
    margin: 0;
  }
  .brand-name {
    top: 358px;
    font-family: "Libre Baskerville", serif;
    font-size: 21px;
    letter-spacing: 3px;
    text-transform: uppercase;
    display: flex;
    justify-content: center;
    align-items: center;
    gap: 12px;
  }
  .brand-dot {
    width: 12px;
    height: 12px;
    border-radius: 50%;
    background: var(--accent);
  }
  .leaf-art {
    position: absolute;
    left: 258px;
    top: 412px;
    width: 200px;
    height: 78px;
    border-radius: 40px;
    background: radial-gradient(ellipse at center, var(--leaf-tone), var(--label) 75%);
  }
  .rule {
    position: absolute;
    left: 196px;
    width: 324px;
    height: 3px;
    background: var(--ink);
  }
  .rule-top { top: 504px; }
  .rule-bottom { top: 558px; }
  .product-name {
    top: 512px;
    font-family: "Libre Baskerville", serif;
    font-size: 29px;
    text-transform: uppercase;
  }
  .slogan {
    top: 574px;
    font-family: "Libre Baskerville", serif;
    font-size: 15px;
    text-transform: uppercase;
    letter-spacing: 0.5px;
  }
  .organic {
    position: absolute;
    left: 150px;
    top: 650px;
    margin: 0;
    font-family: "Didact Gothic", sans-serif;
    font-size: 34px;
    color: var(--ink);
    letter-spacing: 1px;
  }
  .volume {
    position: absolute;
    left: 420px;
    top: 662px;
    margin: 0;
    font-family: "Didact Gothic", sans-serif;
    font-size: 18px;
    color: var(--ink);
  }
</style>
</head>
<body>
  <main class="canvas">
    <svg class="label-shape" width="716" height="1200" viewBox="0 0 716 1200" aria-hidden="true">
      <path d="M150,330 C150,240 260,220 300,270 C330,190 450,190 480,260 C540,220 620,270 590,350 C660,380 660,470 610,500 C670,560 650,660 580,670 C600,760 520,810 460,780 C430,860 320,870 290,800 C230,850 130,820 150,740 C80,720 70,620 130,600 C80,560 90,460 150,450 C100,410 100,340 150,330 Z"
            fill="var(--label)" stroke="var(--ink)" stroke-width="12" stroke-linejoin="round"/>
    </svg>

    <div class="label-text brand-name"><span class="brand-dot"></span>Maple Dew Gala</div>

    <div class="leaf-art" role="img" aria-label="Line drawing of two leaves with a small flowering sprig"></div>

    <div class="rule rule-top"></div>
    <h1 class="label-text product-name">Pure Coconut Oil</h1>
    <div class="rule rule-bottom"></div>
    <p class="label-text slogan">Hydrate your skin and hair</p>

    <p class="organic">ORGANIC</p>
    <p class="volume">236 ML</p>
  </main>
</body>
</html>
```